holloway paving service

Needs to have phone number 0418259730 and email markholloway@brightmail.com.au.
ABN 62318470915
name mark holloway

For all your concreting solutions
Excavation
Exposed & colour concrete
House & shed slabs
Driveways
Landing & steps

Contact Information for Business Card

ph 0418259730
email markholloway@brightmail.com.au.
ABN 62318470915
name mark holloway

```html
<!DOCTYPE html>
<html lang="en">
<head>
<meta charset="utf-8">
<title>Holloway Paving Service – Business Card</title>
<link rel="stylesheet" href="https://fonts.googleapis.com/css2?family=Roboto+Condensed:wght@400;700&family=Roboto:wght@400;500&display=swap">
<style>
  :root{
    --orange:#ee6a1f;
    --orange-light:#f58a3a;
    --orange-dark:#e85a17;
    --grey:#7b7b7b;
    --ink:#4a4a4a;
    --paper:#f7f7f5;
    --backdrop:#e7e4df;
  }
  *{box-sizing:border-box;margin:0;padding:0}
  html,body{width:1200px;height:886px;overflow:hidden;background:var(--backdrop)}
  body{position:relative;font-family:"Roboto",sans-serif}

  .card{position:absolute;top:293px;width:520px;height:300px;overflow:hidden;box-shadow:0 6px 18px rgba(0,0,0,.18)}
  .card--front{left:50px;background:var(--paper)}
  .card--back{left:630px;background:linear-gradient(160deg,var(--orange-light),var(--orange-dark));color:#fff}

  /* front */
  .side-strip{position:absolute;left:0;top:0;width:66px;height:100%;background:var(--orange)}
  .side-strip__top{position:absolute;left:0;top:0;width:66px;height:78px;background:var(--grey)}
  .brand-square{position:absolute;left:14px;top:58px;width:38px;height:38px;background:#fff}
  .side-icons{position:absolute;left:0;top:0;width:66px;height:100%}

  .company{position:absolute;left:92px;top:28px;font-family:"Roboto Condensed",sans-serif;font-weight:700;line-height:1}
  .company__name{color:var(--orange);font-size:17px;letter-spacing:.2px}
  .company__sub{display:flex;align-items:center;gap:6px;color:var(--grey);font-size:13px;letter-spacing:1.5px;margin-top:3px}
  .company__sub::before,.company__sub::after{content:"";display:block;width:28px;height:1px;background:var(--grey)}
  .company__phone{color:var(--orange);font-size:13px;margin-top:3px;letter-spacing:.5px;font-weight:400}

  .abn{position:absolute;right:22px;top:30px;font-family:"Roboto Condensed",sans-serif;font-size:12px;color:var(--ink);letter-spacing:.3px}

  .person{position:absolute;left:92px;top:168px;font-family:"Roboto Condensed",sans-serif}
  .person__name{color:var(--orange);font-size:24px;font-weight:700;letter-spacing:.3px;line-height:1}
  .contacts{list-style:none;margin-top:16px;font-size:12px;color:var(--ink);line-height:18px;font-family:"Roboto",sans-serif}

  /* back */
  .faint-square{position:absolute;left:70px;top:-40px;width:170px;height:170px;background:rgba(255,255,255,.14)}
  .back-brand{position:absolute;left:34px;bottom:34px;font-family:"Roboto Condensed",sans-serif;line-height:1}
  .back-brand__name{font-size:18px;font-weight:700;letter-spacing:.3px}
  .back-brand__sub{font-size:15px;font-weight:700;letter-spacing:2px;margin-top:3px}
  .back-brand__phone{font-size:13px;letter-spacing:1.5px;margin-top:4px}
  .back-brand__web{font-size:11px;letter-spacing:3px;margin-top:5px}
  .services{position:absolute;right:30px;top:110px;list-style:none;text-align:right;font-family:"Roboto",sans-serif;font-size:13px;line-height:19px}
  .services li::after{content:"";display:inline-block;width:4px;height:4px;background:#fff;margin-left:7px;vertical-align:middle}
</style>
</head>
<body>

<section class="card card--front" aria-label="Business card front">
  <div class="side-strip"></div>
  <div class="side-strip__top"></div>
  <div class="brand-square"></div>
  <svg class="side-icons" viewBox="0 0 66 300" aria-hidden="true">
    <g fill="#fff">
      <circle cx="33" cy="173" r="4"/>
      <path d="M26 185a7 6 0 0 1 14 0z"/>
      <path d="M28 214c1 4 4 7 8 8l2-2-2-2-2 1c-1-1-3-3-3-4l1-2-2-2z"/>
      <rect x="27" y="231" width="12" height="8" rx="1"/>
      <circle cx="33" cy="255" r="6"/>
    </g>
    <path d="M27 232l6 4 6-4" stroke="var(--orange)" stroke-width="1" fill="none"/>
    <path d="M27 255h12M33 249v12" stroke="var(--orange)" stroke-width="1"/>
  </svg>

  <div class="company">
    <div class="company__name">HOLLOWAY PAVING</div>
    <div class="company__sub">SERVICE</div>
    <div class="company__phone">0418259730</div>
  </div>

  <div class="abn">ABN 62318470915</div>

  <div class="person">
    <div class="person__name">MARK HOLLOWAY</div>
    <ul class="contacts">
      <li>0418259730</li>
      <li>markholloway@brightmail.com.au</li>
      <li>www.hollowaypaving.com.au</li>
    </ul>
  </div>
</section>

<section class="card card--back" aria-label="Business card back">
  <div class="faint-square"></div>
  <div class="back-brand">
    <div class="back-brand__name">HOLLOWAY PAVING</div>
    <div class="back-brand__sub">SERVICE</div>
    <div class="back-brand__phone">0418259730</div>
    <div class="back-brand__web">www.hollowaypaving.com.au</div>
  </div>
  <ul class="services">
    <li>Excavation</li>
    <li>Exposed &amp; colour concrete</li>
    <li>House &amp; shed slabs</li>
    <li>Driveways</li>
    <li>Landing &amp; steps</li>
  </ul>
</section>

</body>
</html>
```